Business Card Design Project

I need a business card designed from scratch. I have an existing logo that I can upload in Illustrator for modification or redesign.

The Company is called Query Lanterns http://querylanterns.com.au and we provide Search Engine Optimization services to Australian businesses. The current logo signifies an increase in visitors, profits etc...

There are no restrictions as to the redesign - colours, style etc are all open to change.

Cards will be full colour and one sided printed at http://www.cardmoxel.com.au so check their requirements for file format and sizes etc.

I will expect all original files upon completion of project.

Target Market(s)

Any business with a web site looking to improve their search engine rankings

Industry/Entity Type

Business

Requirements
Must have
• I like modern, sleek designs. Clean, not fussy, uncluttered.

```html
<!DOCTYPE html>
<html lang="en">
<head>
<meta charset="utf-8">
<title>Query Lanterns – Business Card</title>
<link href="https://fonts.googleapis.com/css2?family=Source+Sans+3:wght@400;600;700;800&display=swap" rel="stylesheet">
<style>
  :root {
    --brand-blue: #1a6fb5;
    --brand-yellow: #f2c21b;
    --brand-yellow-light: #f4dc4a;
    --ink: #222222;
    --card-white: #ffffff;
    --backdrop: #e9e4d8;
    --card-shadow: 0 2px 6px rgba(0,0,0,0.18);
  }
  * { margin: 0; padding: 0; box-sizing: border-box; }
  html, body {
    width: 1200px; height: 686px; overflow: hidden;
    background: var(--backdrop);
    font-family: "Source Sans 3", sans-serif;
  }
  .canvas { position: relative; width: 1200px; height: 686px; }

  .card {
    position: absolute;
    width: 523px; height: 298px;
    background: var(--card-white);
    box-shadow: var(--card-shadow);
    overflow: hidden;
  }
  .card--front { left: 64px; top: 129px; }
  .card--back { left: 611px; top: 298px; }

  .accent { position: absolute; }
  .accent--top-bar {
    left: 178px; top: 0; width: 321px; height: 9px;
    background: linear-gradient(90deg, var(--brand-yellow-light), var(--brand-yellow));
  }
  .accent--top-block { left: 459px; top: 0; width: 64px; height: 20px; background: var(--brand-blue); }
  .accent--side-yellow {
    left: 0; top: 214px; width: 10px; height: 69px;
    background: linear-gradient(180deg, var(--brand-yellow-light), var(--brand-yellow));
  }
  .accent--side-blue { left: 0; top: 238px; width: 21px; height: 60px; background: var(--brand-blue); }
  .accent--side-yellow { z-index: 2; }

  .wordmark {
    position: absolute;
    display: flex; align-items: center; gap: 10px;
    color: var(--brand-blue);
    font-weight: 700;
    line-height: 1;
    white-space: nowrap;
  }
  .wordmark__dot { border-radius: 50%; background: var(--brand-yellow); flex: none; }
  .card--front .wordmark { left: 58px; top: 78px; font-size: 34px; }
  .card--front .wordmark__dot { width: 18px; height: 18px; }
  .card--back .wordmark { left: 0; right: 0; top: 124px; justify-content: center; font-size: 46px; }
  .card--back .wordmark__dot { width: 24px; height: 24px; }

  .contact {
    position: absolute; right: 56px; top: 0;
    text-align: right;
  }
  .contact__name {
    position: absolute; right: 0; top: 131px; white-space: nowrap;
    color: var(--brand-blue); font-weight: 700; font-size: 18px;
  }
  .contact__title {
    position: absolute; right: 0; top: 152px;
    color: var(--brand-yellow); font-weight: 700; font-size: 13px;
  }
  .contact__line {
    position: absolute; right: 0; white-space: nowrap;
    display: flex; align-items: center; gap: 5px;
    color: var(--ink); font-size: 13px;
  }
  .contact__line svg { width: 11px; height: 11px; flex: none; }
  .contact__line--phone { top: 180px; }
  .contact__line--email { top: 198px; }
  .contact__line--web { top: 215px; }
  .contact__address { top: 241px; right: 16px; }
</style>
</head>
<body>
<main class="canvas">

  <section class="card card--front" aria-label="Card front">
    <div class="accent accent--top-bar"></div>
    <div class="accent accent--top-block"></div>
    <div class="accent accent--side-yellow"></div>
    <div class="accent accent--side-blue"></div>

    <div class="wordmark"><span class="wordmark__dot"></span>Query Lanterns</div>

    <div class="contact" style="width:0;height:298px;right:56px;">
      <p class="contact__name">Your Name</p>
      <p class="contact__title">Title</p>
      <p class="contact__line contact__line--phone" style="right:-16px;">123-456-7890
        <svg viewBox="0 0 12 12" aria-hidden="true"><path d="M2.5 1.2 4.3 3 3.4 4.3c.6 1.6 1.8 2.8 3.4 3.5L8.1 6.8 10 8.6 9 10.6C5 10.6 1.3 6.9 1.2 2.3Z" fill="none" stroke="var(--brand-blue)" stroke-width="1.3" stroke-linejoin="round"/></svg>
      </p>
      <p class="contact__line contact__line--email" style="right:-16px;">inquiry@querylanterns.com.au
        <svg viewBox="0 0 12 12" aria-hidden="true"><rect x="0.5" y="2.5" width="11" height="7.5" fill="var(--brand-blue)"/><path d="M0.8 3 6 7 11.2 3" fill="none" stroke="#fff" stroke-width="1"/></svg>
      </p>
      <p class="contact__line contact__line--web" style="right:-16px;">www.querylanterns.com.au
        <svg viewBox="0 0 12 12" aria-hidden="true"><g fill="none" stroke="var(--brand-blue)" stroke-width="1"><circle cx="6" cy="6" r="5.2"/><ellipse cx="6" cy="6" rx="2.3" ry="5.2"/><path d="M0.8 6h10.4M1.8 3.3h8.4M1.8 8.7h8.4"/></g></svg>
      </p>
      <p class="contact__line contact__address">Street name City, State, zip code</p>
    </div>
  </section>

  <section class="card card--back" aria-label="Card back">
    <div class="wordmark"><span class="wordmark__dot"></span>Query Lanterns</div>
  </section>

</main>
</body>
</html>
```